holloway paving service

Needs to have phone number 0418259730 and email markholloway@brightmail.com.au.
ABN 62318470915
name mark holloway

For all your concreting solutions
Excavation
Exposed & colour concrete
House & shed slabs
Driveways
Landing & steps

Contact Information for Business Card

ph 0418259730
email markholloway@brightmail.com.au.
ABN 62318470915
name mark holloway

```html
<!DOCTYPE html>
<html lang="en">
<head>
<meta charset="UTF-8">
<title>Holloway Paving Service – Business Card</title>
<link rel="stylesheet" href="https://fonts.googleapis.com/css2?family=Montserrat:wght@400;500;700&display=swap">
<style>
  :root {
    --orange: #ec6d2a;
    --grey: #6b6b6b;
    --text: #4a4a4a;
    --card: #ffffff;
    --stage: #e9e7e3;
  }
  * { margin: 0; padding: 0; box-sizing: border-box; }
  html, body {
    width: 1200px; height: 886px; overflow: hidden;
    background: var(--stage);
    font-family: "Montserrat", sans-serif;
  }
  .sheet {
    width: 1200px; height: 886px;
    display: flex; align-items: center; justify-content: center; gap: 40px;
  }
  .card {
    position: relative;
    width: 540px; height: 310px;
    background: var(--card);
    box-shadow: 0 6px 20px rgba(0,0,0,.12);
  }

  /* Front */
  .front .brand-block {
    position: absolute; left: 46px; top: 110px; width: 190px;
    display: flex; flex-direction: column; align-items: flex-start; gap: 12px;
  }
  .brand-square { width: 44px; height: 44px; background: var(--orange); }
  .brand-name {
    font-weight: 700; font-size: 17px; line-height: 1.25;
    color: var(--grey); text-transform: uppercase; letter-spacing: .5px;
  }
  .front .divider {
    position: absolute; left: 262px; top: 40px; width: 2px; height: 230px;
    background: var(--orange);
  }
  .front .person {
    position: absolute; left: 290px; top: 70px; right: 24px;
  }
  .person-name {
    color: var(--orange); font-weight: 700; font-size: 20px;
    text-transform: uppercase; letter-spacing: .5px;
  }
  .person-rule { height: 2px; width: 180px; background: var(--orange); margin: 12px 0 16px; }
  .contact-list { list-style: none; display: flex; flex-direction: column; gap: 7px; }
  .contact-list li {
    display: flex; align-items: center; gap: 8px;
    font-size: 11.5px; color: var(--text);
  }
  .contact-list svg { width: 11px; height: 11px; flex: none; fill: var(--orange); }
  .contact-list .abn { padding-left: 19px; }

  /* Back */
  .back .services {
    position: absolute; left: 40px; top: 78px;
    list-style: none; display: flex; flex-direction: column; gap: 9px;
    font-size: 12px; color: var(--text);
  }
  .back .services .lead { color: var(--grey); font-weight: 500; margin-bottom: 4px; }
  .back .identity {
    position: absolute; right: 36px; top: 52px; width: 230px;
    display: flex; flex-direction: column; align-items: center; text-align: center;
  }
  .back .brand-square { width: 56px; height: 56px; }
  .back .identity-rule { width: 150px; height: 2px; background: var(--orange); margin: 18px 0 14px; }
  .back .brand-name { color: var(--orange); font-size: 16px; }
  .back .phone {
    margin-top: 10px; font-size: 14px; color: var(--orange); letter-spacing: 1px;
  }
  .back .phone-rules { display: flex; align-items: center; gap: 8px; margin-top: 6px; }
  .back .phone-rules span { width: 60px; height: 1.5px; background: var(--grey); }
</style>
</head>
<body>
<main class="sheet">

  <section class="card front" aria-label="Business card front">
    <div class="brand-block">
      <div class="brand-square"></div>
      <div class="brand-name">Holloway Paving Service</div>
    </div>
    <div class="divider"></div>
    <div class="person">
      <h1 class="person-name">Mark Holloway</h1>
      <div class="person-rule"></div>
      <ul class="contact-list">
        <li><svg viewBox="0 0 24 24"><path d="M6.6 10.8a15 15 0 0 0 6.6 6.6l2.2-2.2a1 1 0 0 1 1-.25 11.4 11.4 0 0 0 3.6.57 1 1 0 0 1 1 1V20a1 1 0 0 1-1 1A17 17 0 0 1 3 4a1 1 0 0 1 1-1h3.5a1 1 0 0 1 1 1c0 1.25.2 2.45.57 3.57a1 1 0 0 1-.25 1z"/></svg>0418259730</li>
        <li><svg viewBox="0 0 24 24"><path d="M2 5h20v14H2zm2 2v.5l8 5 8-5V7l-8 5z"/></svg>markholloway@brightmail.com.au</li>
        <li><svg viewBox="0 0 24 24"><circle cx="12" cy="12" r="10"/></svg>www.hollowaypaving.com.au</li>
        <li class="abn">ABN 62318470915</li>
      </ul>
    </div>
  </section>

  <section class="card back" aria-label="Business card back">
    <ul class="services">
      <li class="lead">For all your concreting solutions</li>
      <li>Excavation</li>
      <li>Exposed &amp; colour concrete</li>
      <li>House &amp; shed slabs</li>
      <li>Driveways</li>
      <li>Landing &amp; steps</li>
    </ul>
    <div class="identity">
      <div class="brand-square"></div>
      <div class="identity-rule"></div>
      <div class="brand-name">Holloway Paving Service</div>
      <div class="phone-rules"><span></span><span></span></div>
      <div class="phone">0418259730</div>
    </div>
  </section>

</main>
</body>
</html>
```